Briefpapier und Visitenkarten
Zielgruppe
In erster Linie mir selbst.
Aufgabenstellung
Gestaltung von Visitenkarten und Briefpapier.
Visitenkarten: Gestaltung beidseitig und in Pantone Farben
Briefpapier: Gestaltung einseitig und in Pantone Farben
Briefpapier und Visitenkarten sollen ein Design haben.

```html
<!DOCTYPE html>
<html lang="de">
<head>
<meta charset="utf-8">
<title>Korlan Werbeagentur – Briefpapier und Visitenkarten</title>
<link href="https://fonts.googleapis.com/css2?family=Open+Sans:wght@400;600;700&display=swap" rel="stylesheet">
<style>
  :root{
    --paper:#ffffff;
    --stage:#ffffff;
    --brand-grey:#a9a9a9;
    --text-dark:#555555;
    --text-soft:#bdbdbd;
    --deco:#ececec;
    --band-dark:#6d6d6d;
    --band-mid:#9a9a9a;
    --card-back:#c6c6c6;
    --card-back-deco:#dadada;
  }
  *{box-sizing:border-box;margin:0;padding:0}
  html,body{width:1200px;height:838px;overflow:hidden;background:var(--stage)}
  body{position:relative;font-family:"Open Sans",Arial,sans-serif;color:var(--text-dark)}
  .sheet{position:absolute;background:var(--paper);overflow:hidden;box-shadow:2px 3px 6px rgba(0,0,0,.28)}
  .deco{position:absolute;border-radius:50%;background:var(--deco)}
  .brand{position:absolute;text-align:center}
  .brand-dot{display:block;margin:0 auto 8px;border-radius:50%;background:var(--brand-grey)}
  .brand-name{display:block;font-weight:600;color:var(--brand-grey);text-transform:uppercase;letter-spacing:1.5px;white-space:nowrap}
  .band{position:absolute;left:0;right:0;bottom:0;color:#fff;white-space:nowrap;display:flex;align-items:center}
  .sep{display:inline-block;margin:0 4px;opacity:.8}

  /* letterhead */
  .letterhead{left:76px;top:32px;width:542px;height:766px}
  .letterhead .brand{left:245px;top:36px;width:240px}
  .letterhead .brand-dot{width:44px;height:44px}
  .letterhead .brand-name{font-size:16.5px}
  .sender-line{position:absolute;left:51px;top:103px;font-size:5.5px;color:#777}
  .sender-line b{font-weight:700}
  .contact{position:absolute;line-height:1.4}
  .contact p{margin-bottom:5px}
  .contact strong{font-weight:700}
  .letterhead .contact{left:413px;top:138px;font-size:7.5px}
  .side-list{position:absolute;left:414px;top:283px;list-style:none;font-size:10px;color:var(--text-soft);line-height:22px}
  .fold-mark{position:absolute;left:0;top:270px;width:13px;height:1px;background:#999}
  .letterhead .deco{left:276px;top:420px;width:316px;height:316px}
  .letterhead .band{height:47px;background:var(--band-dark);padding-left:50px;font-size:7.5px}

  /* business card front */
  .card-front{left:696px;top:139px;width:419px;height:271px}
  .card-front .brand{left:40px;top:17px;width:265px}
  .card-front .brand-dot{width:44px;height:44px}
  .card-front .brand-name{font-size:16.5px}
  .card-front .contact{left:46px;top:113px;font-size:9.5px}
  .card-front .contact p{margin-bottom:6px}
  .card-front .deco{left:280px;top:90px;width:176px;height:176px}
  .card-front .band{height:41px;background:var(--band-mid);border-top:2px solid #b5b5b5;padding-left:46px;font-size:9.5px}

  /* business card back */
  .card-back{left:696px;top:432px;width:419px;height:271px;background:var(--card-back)}
  .card-back .deco{left:136px;top:58px;width:150px;height:150px;background:var(--card-back-deco)}
</style>
</head>
<body>

<section class="sheet letterhead" aria-label="Briefpapier">
  <div class="brand">
    <span class="brand-dot"></span>
    <span class="brand-name">Korlan Werbeagentur</span>
  </div>
  <p class="sender-line"><b>Korlan Werbeagentur</b><span class="sep">·</span>Lindenweg 14<span class="sep">·</span>D-53911 Halvenrod</p>
  <div class="contact">
    <p><strong>Korlan Werbeagentur</strong><br>Inh. Jonas Korlan</p>
    <p>Lindenweg 14<br>D-53911 Halvenrod</p>
    <p>E-Mail: korlan@korlanwa.de<br>Website: www.korlanwa.de</p>
  </div>
  <ul class="side-list">
    <li>Beispiel</li><li>Muster</li><li>TextTextText</li>
    <li>Beispiel</li><li>Muster</li><li>TextTextText</li>
  </ul>
  <span class="fold-mark"></span>
  <span class="deco"></span>
  <div class="band">Musterbank<span class="sep">·</span>Ktn. XXX XXX XXX<span class="sep">·</span>BLZ XXX XXX XXX<span class="sep">·</span>Sonstiges<span class="sep">·</span>Sonstiges<span class="sep">·</span>Sonstiges<span class="sep">·</span>Sonstiges<span class="sep">·</span>Sonstiges<span class="sep">·</span>Sonst</div>
</section>

<section class="sheet card-front" aria-label="Visitenkarte Vorderseite">
  <span class="deco"></span>
  <div class="brand">
    <span class="brand-dot"></span>
    <span class="brand-name">Korlan Werbeagentur</span>
  </div>
  <div class="contact">
    <p><strong>Korlan Werbeagentur</strong><br>Inh. Jonas Korlan</p>
    <p>Lindenweg 14<br>D-53911 Halvenrod</p>
    <p>E-Mail: korlan@korlanwa.de<br>Website: www.korlanwa.de</p>
  </div>
  <div class="band">Beispiel<span class="sep">·</span>Muster<span class="sep">·</span>TextTextText<span class="sep">·</span>Beispiel<span class="sep">·</span>Muster<span class="sep">·</span>TextTextTextTe</div>
</section>

<section class="sheet card-back" aria-label="Visitenkarte Rückseite">
  <span class="deco"></span>
</section>

</body>
</html>
```